Brightway Haus Inc. Business Card Design

Brightway Haus Inc. is in search of a great clean design for our business cards!

Looking to incorporate our full logo and watermark on side one (however, I am open to having the text and watermark separated within the design.)

On side two, I am looking to have contact information (Name, Position, Phone #, Email, Website (www.thebrightwayhaus.ca). Can have the logo and/or watermark as part of the design if applicable.

Please add tagline "Where Shine Counts" on either side 1 or 2. This tagline can be in a sans serif, serif or cursive font as long as it compliments overall design. Capitalization can be title or sentence case depending on how it fits within the design.

Get creative!! Looking for a clean, crisp, premium design! Looking for a glossy card finish with spot UV features when printed. Cards will also be printed with rounded corners. Standard dimensions (3.5 x 2).

Target Market(s)

B2B - primary clients are business owners or property management corporations. (residential jobs are few and far between)

Industry/Entity Type

Business

Contact Information for Business Card

- clean, crisp design
- double sided
- spot UV accents and glossy finish upon printing
- standard business card size (3.5 x 2) with rounded corners
- please see project description for requirements per side

Font styles to use
Sans Serif

Requirements
Must have
• - adequate bleeds with print ready files
• - cohesive design elements between side 1 & 2
• - spot UV elements (can be on both sides or just one, use your discretion)
• - colour pallet should match the logo file provided
• - incorporate tagline "where shine counts" (this tagline can be in a serif or sans serif font as long as it is complimentary to the overall design.
Nice to have
• - Premium elements with a clean design
Should not have
• - Please omit cartoon or whimsical like designs, think premium.
• - Colours should not stray from the pallet of the provided logo.

```html
<!DOCTYPE html>
<html lang="en">
<head>
<meta charset="utf-8">
<title>Brightway Haus Inc. Business Card</title>
<link href="https://fonts.googleapis.com/css2?family=Roboto:wght@400;500;700;900&display=swap" rel="stylesheet">
<style>
  :root {
    --backdrop: #3b3b3d;
    --card: #262628;
    --card-gloss: #303033;
    --teal: #1aa9ad;
    --silver: #a7a8aa;
    --text-light: #d2d3d5;
    --text-muted: #a9aaac;
  }
  * { margin: 0; padding: 0; box-sizing: border-box; }
  html, body { width: 799px; height: 1200px; overflow: hidden; }
  body {
    background: var(--backdrop);
    font-family: 'Roboto', sans-serif;
    position: relative;
  }
  .card {
    position: absolute;
    left: 80px;
    width: 640px;
    height: 366px;
    background: var(--card);
    border-radius: 14px;
    overflow: hidden;
    box-shadow: 0 18px 40px rgba(0,0,0,0.45);
  }
  .card--front { top: 150px; }
  .card--back { top: 684px; }

  /* Front: spot UV name mark */
  .front-mark {
    position: absolute;
    left: 50%; top: 50%;
    transform: translate(-50%, -50%);
    display: flex; align-items: center; gap: 18px;
  }
  .front-mark__square {
    width: 70px; height: 70px;
    background: var(--card-gloss);
  }
  .front-mark__name {
    font-weight: 700;
    font-size: 34px;
    color: var(--card-gloss);
    letter-spacing: 0.5px;
  }

  /* Back */
  .brand {
    position: absolute;
    left: 40px; top: 30px;
    display: flex; align-items: center; gap: 12px;
  }
  .brand__square { width: 44px; height: 44px; background: var(--teal); }
  .brand__name {
    font-weight: 900;
    font-size: 44px;
    color: var(--teal);
    letter-spacing: -0.5px;
    line-height: 1;
  }
  .accent-arc {
    position: absolute;
    left: -22px; top: 104px;
    width: 44px; height: 70px;
    border-radius: 0 35px 35px 0;
    background: var(--teal);
    left: 0;
    width: 20px;
  }
  .person { position: absolute; left: 70px; top: 116px; }
  .person__name { font-weight: 700; font-size: 24px; color: var(--teal); }
  .person__role { font-size: 13px; color: var(--text-muted); margin-top: 4px; }
  .contacts {
    position: absolute; left: 48px; top: 182px;
    list-style: none;
  }
  .contacts li {
    display: flex; align-items: center; gap: 12px;
    font-size: 15px; color: var(--text-light);
    height: 24px;
  }
  .contacts svg { width: 13px; height: 13px; fill: var(--silver); }
  .contacts .web-accent { color: var(--teal); }
  .address {
    position: absolute; right: 34px; top: 262px;
    text-align: right;
    font-size: 15px; line-height: 22px;
    color: var(--text-light);
  }
  .band-teal {
    position: absolute; left: 0; bottom: 0;
    width: 60%; height: 12px;
    background: var(--teal);
  }
  .band-silver {
    position: absolute; right: 0; bottom: 0;
    width: 48%; height: 36px;
    background: var(--silver);
    clip-path: polygon(26px 0, 100% 0, 100% 100%, 0 100%);
    display: flex; align-items: center; justify-content: flex-end;
    padding-right: 34px;
  }
  .tagline { font-size: 15px; color: #f2f2f2; letter-spacing: 0.6px; }
</style>
</head>
<body>
  <section class="card card--front" aria-label="Card front">
    <div class="front-mark">
      <div class="front-mark__square"></div>
      <span class="front-mark__name">Brightway Haus Inc.</span>
    </div>
  </section>

  <section class="card card--back" aria-label="Card back">
    <div class="brand">
      <div class="brand__square"></div>
      <span class="brand__name">Brightway Haus Inc.</span>
    </div>
    <div class="accent-arc"></div>
    <div class="person">
      <div class="person__name">Marlowe Tennant</div>
      <div class="person__role">Managing Director</div>
    </div>
    <ul class="contacts">
      <li>
        <svg viewBox="0 0 16 16"><path d="M3 1h3l1.5 4-2 1.3a9 9 0 0 0 4.2 4.2L11 8.5 15 10v3a2 2 0 0 1-2 2A12 12 0 0 1 1 3a2 2 0 0 1 2-2z"/></svg>
        1800-555-0147
      </li>
      <li>
        <svg viewBox="0 0 16 16"><path d="M1 3h14v10H1zM2 4.2v.3l6 4 6-4v-.3z"/></svg>
        marlowe@brightwayhaus.ca
      </li>
      <li>
        <svg viewBox="0 0 16 16"><circle cx="8" cy="8" r="7"/></svg>
        <span>www.<span class="web-accent">thebrightwayhaus</span>.ca</span>
      </li>
    </ul>
    <div class="address">48, Larkfield Road<br>Unit 7, Canada 204</div>
    <div class="band-teal"></div>
    <div class="band-silver"><span class="tagline">Where Shine Counts</span></div>
  </section>
</body>
</html>
```